Home Remodeling company needs a business card design

we need a business card design for home remodeling company in hamilton county, indiana USA. we offers a wide range of construction services including whole house renovations, Design and Build Basements and Kitchen and Bathroom Remodeling . we would like to see designs for both site of business card that use the same color of the company logo and also including all information below :
1- Karim Feltous CEO / General Contractor
2- all company contacts Telephone numbers ( 1-888-DULOM-47 ) ( 317-555-0193) email address ( info@dulomhome.com) website ( www.dulomhome.com ) and social media logos (Facebook- twitter- google plus )
3- company logo
4- licensed . insured . bonded

```html
<!DOCTYPE html>
<html lang="en">
<head>
<meta charset="utf-8">
<title>Dulom Home Remodeling – Business Card</title>
<link rel="stylesheet" href="https://fonts.googleapis.com/css2?family=Open+Sans:wght@400;600&display=swap">
<style>
  :root {
    --page-bg: #e9e6e1;
    --card-black: #0d0d0d;
    --card-black-soft: #1c1c1c;
    --brand-red: #c8323a;
    --wave-grey: #3a3a3c;
    --text-white: #f4f4f4;
    --name-grey: #9a9a9a;
  }
  * { box-sizing: border-box; margin: 0; padding: 0; }
  html, body { width: 1200px; height: 900px; overflow: hidden; }
  body {
    background: var(--page-bg);
    font-family: "Open Sans", Arial, sans-serif;
    position: relative;
  }
  .card {
    position: absolute;
    width: 520px;
    height: 297px;
    border-radius: 4px;
    overflow: hidden;
    background: radial-gradient(ellipse at 45% 40%, var(--card-black-soft) 0%, var(--card-black) 75%);
    box-shadow: 0 10px 28px rgba(0,0,0,0.25);
  }
  .card-front { left: 80px; top: 120px; }
  .card-back { left: 600px; top: 480px; }

  /* Company name placeholder: one colour, one weight */
  .company-name {
    font-weight: 600;
    color: var(--name-grey);
    line-height: 1.2;
    white-space: nowrap;
  }

  /* Front */
  .card-front .company-name {
    position: absolute;
    left: 0; right: 0;
    top: 100px;
    text-align: center;
    font-size: 32px;
  }
  .credentials {
    position: absolute;
    left: 0; right: 0;
    top: 168px;
    text-align: center;
    font-size: 18px;
    font-weight: 600;
    color: var(--text-white);
  }
  .credentials .accent { color: var(--brand-red); }

  /* Back */
  .wave {
    position: absolute;
    inset: 0;
    width: 520px;
    height: 297px;
  }
  .person {
    position: absolute;
    left: 34px;
    top: 30px;
  }
  .person-name {
    color: var(--brand-red);
    font-size: 17px;
    font-weight: 600;
    line-height: 1.3;
  }
  .person-title {
    color: var(--text-white);
    font-size: 12px;
    margin-left: 10px;
  }
  .card-back .company-name {
    position: absolute;
    right: 28px;
    top: 70px;
    font-size: 20px;
  }

  .contacts {
    position: absolute;
    left: 40px;
    top: 148px;
    list-style: none;
  }
  .contacts li {
    display: flex;
    align-items: center;
    gap: 8px;
    color: var(--text-white);
    font-size: 14px;
    line-height: 21px;
  }
  .contacts svg { width: 11px; height: 11px; flex: none; }

  .social {
    position: absolute;
    right: 22px;
    top: 178px;
    display: flex;
    gap: 9px;
  }
  .social span {
    width: 24px; height: 24px;
    border-radius: 50%;
    background: var(--text-white);
  }
</style>
</head>
<body>

  <section class="card card-front" aria-label="Business card front">
    <p class="company-name">Dulom Home Remodeling</p>
    <p class="credentials">Licensed <span class="accent">. Insured .</span> Bonded</p>
  </section>

  <section class="card card-back" aria-label="Business card back">
    <svg class="wave" viewBox="0 0 520 297" preserveAspectRatio="none" aria-hidden="true">
      <path d="M0,262 C140,300 300,160 520,118 L520,297 L0,297 Z" fill="var(--wave-grey)"/>
      <path d="M0,286 C160,300 300,175 520,142 L520,297 L0,297 Z" fill="var(--brand-red)"/>
    </svg>

    <div class="person">
      <p class="person-name">Karim Feltous</p>
      <p class="person-title">CEO / General Contractor</p>
    </div>

    <p class="company-name">Dulom Home Remodeling</p>

    <ul class="contacts">
      <li>
        <svg viewBox="0 0 24 24" aria-hidden="true"><path fill="var(--brand-red)" d="M6.6 10.8a15.1 15.1 0 0 0 6.6 6.6l2.2-2.2c.3-.3.7-.4 1-.2 1.1.4 2.3.6 3.6.6.6 0 1 .4 1 1V20c0 .6-.4 1-1 1A17 17 0 0 1 3 4c0-.6.4-1 1-1h3.5c.6 0 1 .4 1 1 0 1.3.2 2.5.6 3.6.1.3 0 .7-.2 1z"/></svg>
        1-888-DULOM-47
      </li>
      <li>
        <svg viewBox="0 0 24 24" aria-hidden="true"><path fill="var(--brand-red)" d="M6.6 10.8a15.1 15.1 0 0 0 6.6 6.6l2.2-2.2c.3-.3.7-.4 1-.2 1.1.4 2.3.6 3.6.6.6 0 1 .4 1 1V20c0 .6-.4 1-1 1A17 17 0 0 1 3 4c0-.6.4-1 1-1h3.5c.6 0 1 .4 1 1 0 1.3.2 2.5.6 3.6.1.3 0 .7-.2 1z"/></svg>
        317-555-0193
      </li>
      <li>
        <svg viewBox="0 0 24 24" aria-hidden="true"><path fill="var(--brand-red)" d="M2 5h20v14H2z"/><path d="M2 5l10 8 10-8" fill="none" stroke="var(--card-black)" stroke-width="2"/></svg>
        info@dulomhome.com
      </li>
      <li>
        <svg viewBox="0 0 24 24" aria-hidden="true"><g fill="none" stroke="var(--brand-red)" stroke-width="3" stroke-linecap="round"><path d="M10 14l4-4"/><path d="M8 11l-3 3a3.5 3.5 0 0 0 5 5l3-3"/><path d="M16 13l3-3a3.5 3.5 0 0 0-5-5l-3 3"/></g></svg>
        www.dulomhome.com
      </li>
    </ul>

    <div class="social" aria-label="Social media">
      <span></span><span></span><span></span>
    </div>
  </section>

</body>
</html>
```